New Webpage for High Class Expert Witness Services Company

We are looking for a minimalist design for a webpage that just has our logo and an entry form offer to connect with one of our Liaisons.
The entry form should just ask for Name, Email, Contact Info and Description of Project.

Company Name is: The Marlowe Crest Advisory Services

Number of Pages Required

1 page

```html
<!DOCTYPE html>
<html lang="en">
<head>
<meta charset="utf-8">
<title>The Marlowe Crest Advisory Services — Connect With Us</title>
<link href="https://fonts.googleapis.com/css2?family=Cinzel:wght@400;600;700&family=Manrope:wght@400&family=Roboto:wght@400&display=swap" rel="stylesheet">
<style>
  :root {
    --bg: #111112;
    --bg-soft: #1d1d1f;
    --text: #f4f4f4;
    --text-muted: #b9b9b9;
    --text-dim: #9a9a9a;
    --line: #6a6a6a;
    --field-line: #8c8c8c;
    --silver-light: #e4e4e6;
    --silver-dark: #9d9ea2;
    --ink: #111111;
  }
  * { box-sizing: border-box; margin: 0; padding: 0; }
  html, body { width: 1200px; height: 742px; overflow: hidden; background: var(--bg); }
  .page { position: relative; width: 1200px; height: 742px; overflow: hidden; color: var(--text); }
  .backdrop {
    position: absolute; inset: 0;
    background:
      radial-gradient(ellipse 260px 300px at 250px 330px, #2a2a2c 0%, rgba(30,30,32,0) 70%),
      radial-gradient(ellipse 420px 320px at 960px 420px, #1f1f21 0%, rgba(20,20,22,0) 75%),
      linear-gradient(180deg, #151516 0%, #101011 100%);
  }
  .brand {
    position: absolute; left: 120px; top: 40px;
    display: flex; align-items: center; gap: 12px;
    font-family: "Cinzel", serif; font-weight: 400; color: var(--text-muted);
  }
  .brand-mark { width: 44px; height: 56px; border: 1px solid var(--text-muted); }
  .brand-name { font-size: 24px; line-height: 28px; letter-spacing: 1px; }
  .hero { position: absolute; left: 113px; top: 218px; width: 520px; }
  .hero-eyebrow {
    font-family: "Cinzel", serif; font-size: 15px; letter-spacing: 1.6px;
    color: var(--text-dim); margin-left: 7px;
  }
  .hero-title {
    font-family: "Cinzel", serif; font-weight: 400; font-size: 50px;
    line-height: 51px; letter-spacing: 1.5px; margin-top: 14px;
  }
  .hero-text {
    font-family: "Manrope", sans-serif; font-size: 14px; line-height: 28px;
    color: var(--text-muted); margin-top: 12px; width: 480px;
  }
  .contact {
    position: absolute; left: 715px; top: 124px; width: 378px; height: 438px;
    border: 1px solid var(--line); padding: 34px 0 0 46px;
  }
  .contact-title { font-family: "Cinzel", serif; font-weight: 400; font-size: 23px; letter-spacing: 0.5px; }
  .field {
    display: block; width: 294px; height: 42px; margin-top: 12px;
    border: 1px solid var(--field-line); background: transparent; color: var(--text);
    font-family: "Roboto", sans-serif; font-size: 13px; padding: 0 17px;
  }
  .field::placeholder { color: var(--text); }
  .field:first-of-type { margin-top: 25px; }
  .field-area { height: 88px; padding-top: 11px; resize: none; }
  .submit {
    display: block; width: 297px; height: 44px; margin-top: 13px; border: 0;
    background: linear-gradient(115deg, var(--silver-light) 0%, var(--silver-light) 55%, var(--silver-dark) 80%, #b6b7ba 100%);
    font-family: "Cinzel", serif; font-weight: 700; font-size: 14px; color: var(--ink); letter-spacing: 0.5px;
  }
  .footer {
    position: absolute; left: 0; right: 0; top: 680px; bottom: 0;
    border-top: 1px solid #3a3a3a; text-align: center;
    font-family: "Roboto", sans-serif; font-size: 12px; color: var(--text-dim); padding-top: 20px;
  }
</style>
</head>
<body>
<main class="page">
  <div class="backdrop" role="img" aria-label="Dark textured background with a faint faceted shield and medical network motif"></div>

  <header class="brand">
    <span class="brand-mark"></span>
    <span class="brand-name">MARLOWE CREST<br>ADVISORY SERVICES</span>
  </header>

  <section class="hero">
    <p class="hero-eyebrow">MARLOWE CREST ADVISORY SERVICES</p>
    <h1 class="hero-title">SEAMLESS<br>MEDICAL EXPERT<br>INTEGRATION</h1>
    <p class="hero-text">Lorem ipsum dolor sit amet, consectetur adipiscing elit, sed do eiusmod tempor incididunt ut labore et dolore magna aliqua.</p>
  </section>

  <form class="contact">
    <h2 class="contact-title">CONNECT WITH US</h2>
    <input class="field" type="text" placeholder="Name*">
    <input class="field" type="email" placeholder="Email*">
    <input class="field" type="tel" placeholder="Phone number*">
    <textarea class="field field-area" placeholder="Description of Project"></textarea>
    <button class="submit" type="submit">SUBMIT</button>
  </form>

  <footer class="footer">© 2026 Marlowe Crest Advisory Services. All Rights Reserved</footer>
</main>
</body>
</html>
```